Unique Business Card Design

Unique Business Card design for our orthotic and prosthetic company. Our logo is on our website, color is light blue. Unique shape (artificial leg shaped, vertical, etc..) preferred. Logo, business name, individual name and basic demographics needed.

Industry/Entity Type

Business

Contact Information for Business Card

Logo, Industry, Phone # Logo, "Prosthetic & Orthotic Services" Place to add individual name and contact info

Colors
cee9f5

Requirements
Must have
• The icon must be there, placement of "Prosthetic & Orthotic Services" can be moved
Nice to have
• Like the mix of light blue, and a little darker blue. One design included the icons from my website which was a nice touch

```html
<!DOCTYPE html>
<html lang="en">
<head>
<meta charset="utf-8">
<title>Limbwell Inc. — Business Card</title>
<link rel="stylesheet" href="https://fonts.googleapis.com/css2?family=Roboto:wght@300;400;700&family=Roboto+Condensed:wght@400;700&display=swap">
<style>
  :root {
    --bg: #1f2022;
    --blue: #1f60b0;
    --blue-deep: #174d92;
    --sky: #cee9f5;
    --white: #ffffff;
    --gray: #b9bdc3;
    --ink: #3c4148;
    --ink-soft: #5b616a;
  }
  * { margin: 0; padding: 0; box-sizing: border-box; }
  html, body { width: 1200px; height: 950px; overflow: hidden; }
  body {
    background: var(--bg);
    font-family: "Roboto", Arial, sans-serif;
    position: relative;
  }
  .card {
    position: absolute;
    left: 250px;
    width: 700px;
    height: 400px;
    border-radius: 22px;
    overflow: hidden;
  }
  .card-front { top: 55px; background: var(--white); }
  .card-back  { top: 495px; background: linear-gradient(135deg, var(--blue) 0%, var(--blue-deep) 100%); }
  .card-art { position: absolute; inset: 0; width: 100%; height: 100%; }

  /* front */
  .holder {
    position: absolute; right: 40px; top: 22px; text-align: right; color: var(--white);
  }
  .holder-name { font-family: "Roboto Condensed", Arial, sans-serif; font-size: 30px; font-weight: 400; letter-spacing: .3px; }
  .holder-title { font-size: 15px; margin-top: 2px; letter-spacing: .5px; }

  .brand { position: absolute; display: flex; align-items: center; }
  .brand-mark { border-radius: 50%; flex: none; }
  .brand-name { font-family: "Roboto Condensed", Arial, sans-serif; font-weight: 700; line-height: 1; }
  .brand-tagline { font-family: "Roboto", Arial, sans-serif; font-weight: 400; padding-top: 5px; margin-top: 5px; }

  .card-front .brand { left: 42px; top: 200px; }
  .card-front .brand-mark { width: 76px; height: 76px; background: var(--blue); margin-right: 16px; }
  .card-front .brand-name { font-size: 32px; color: var(--blue); }
  .card-front .brand-tagline { font-size: 15px; color: var(--blue); border-top: 2px solid var(--blue); }

  .contacts { position: absolute; left: 44px; top: 298px; list-style: none; }
  .contacts li { display: flex; align-items: center; font-size: 16px; color: var(--ink-soft); height: 23px; }
  .contacts svg { width: 15px; height: 15px; margin-right: 10px; fill: var(--ink-soft); }

  .address { position: absolute; right: 40px; bottom: 30px; text-align: right; font-size: 16px; color: var(--ink-soft); line-height: 23px; font-style: normal; }

  /* back */
  .card-back .brand { left: 90px; top: 105px; }
  .card-back .brand-mark { width: 116px; height: 116px; background: var(--white); margin-right: 26px; }
  .card-back .brand-name { font-size: 50px; color: var(--white); }
  .card-back .brand-tagline { font-size: 21px; color: var(--white); border-top: 3px solid var(--white); }

  .web { position: absolute; left: 56px; bottom: 50px; display: flex; align-items: center; width: 600px; color: var(--sky); font-size: 17px; letter-spacing: .4px; }
  .web::after { content: ""; flex: 1; height: 1px; background: var(--sky); margin-left: 22px; opacity: .8; }
</style>
</head>
<body>

<section class="card card-front" aria-label="Business card front">
  <svg class="card-art" viewBox="0 0 700 400" aria-hidden="true">
    <path d="M0,0 H700 V92 C600,80 480,62 360,80 C220,102 110,140 0,190 Z" fill="var(--blue)"/>
    <path d="M0,205 C120,150 240,104 380,92 C480,84 580,90 700,104" fill="none" stroke="var(--gray)" stroke-width="7"/>
    <path d="M0,190 C110,140 220,102 360,80" fill="none" stroke="var(--blue-deep)" stroke-width="3" opacity=".6"/>
  </svg>

  <div class="holder">
    <div class="holder-name">Miriam Kessler</div>
    <div class="holder-title">CO LPO</div>
  </div>

  <div class="brand">
    <span class="brand-mark"></span>
    <div>
      <div class="brand-name">LIMBWELL INC.</div>
      <div class="brand-tagline">Prosthetic &amp; Orthotic Services</div>
    </div>
  </div>

  <ul class="contacts">
    <li><svg viewBox="0 0 16 16"><path d="M3 1h3l1.5 4-2 1.2a9 9 0 0 0 4.3 4.3L11 8.5l4 1.5v3a2 2 0 0 1-2 2A12 12 0 0 1 1 3a2 2 0 0 1 2-2z"/></svg>718.555.0140</li>
    <li><svg viewBox="0 0 16 16"><path d="M4 0h8a1 1 0 0 1 1 1v14a1 1 0 0 1-1 1H4a1 1 0 0 1-1-1V1a1 1 0 0 1 1-1zm1 2v10h6V2zm3 11a1 1 0 1 0 0 2 1 1 0 0 0 0-2z"/></svg>718.555.0162</li>
    <li><svg viewBox="0 0 16 16"><path d="M4 0h7v4H4zM1 5h14v8h-3v3H4v-3H1zm4 6v3h6v-3z"/></svg>845.555.0187</li>
    <li><svg viewBox="0 0 16 16"><path d="M0 3h16v10H0zm1.5 1.2V5l6.5 4 6.5-4v-.8L8 8z"/></svg>mkessler@limbwellinc.com</li>
  </ul>

  <address class="address">
    2380 Harbor Ave.<br>
    Brooklyn, NY 11229<br>
    www.limbwellinc.com
  </address>
</section>

<section class="card card-back" aria-label="Business card back">
  <div class="brand">
    <span class="brand-mark"></span>
    <div>
      <div class="brand-name">LIMBWELL INC.</div>
      <div class="brand-tagline">Prosthetic &amp; Orthotic Services</div>
    </div>
  </div>
  <div class="web">www.limbwellinc.com</div>
</section>

</body>
</html>
```